Business Cards for a law firm

Business cards for our law firm. Use our silhoette logo and OAK PARTNERS - check our website (www.oakpartners.example)

Contact Information for Business Card

our silhouette logo, OAK PARTNERS, 800-555-0147, Dorian Pemberton, dorian@oakpartners.example

Requirements
Must have
• our silhouette logo, OAK PARTNERS, 800-555-0147, Dorian Pemberton, dorian@oakpartners.example

```html
<!DOCTYPE html>
<html lang="en">
<head>
<meta charset="utf-8">
<title>Oak Partners – Business Card</title>
<link href="https://fonts.googleapis.com/css2?family=Montserrat:wght@400;500;700&display=swap" rel="stylesheet">
<style>
  :root {
    --navy: #233672;
    --navy-deep: #1e2f66;
    --navy-soft: #3a4f96;
    --ink: #1a1a1a;
    --paper: #ffffff;
    --backdrop: #e9eaee;
  }
  * { box-sizing: border-box; margin: 0; padding: 0; }
  html, body { width: 1200px; height: 900px; overflow: hidden; }
  body {
    background: var(--backdrop);
    font-family: "Montserrat", Arial, sans-serif;
    position: relative;
  }
  .card {
    position: absolute;
    top: 100px;
    width: 400px;
    height: 700px;
    box-shadow: 0 10px 28px rgba(0,0,0,.18);
  }
  .card-front { left: 160px; background: var(--paper); }
  .card-back  { left: 640px; background: var(--navy-deep); }

  .firm-name {
    position: absolute;
    top: 70px;
    left: 0; right: 0;
    text-align: center;
    color: var(--navy);
    font-weight: 700;
    font-size: 34px;
    letter-spacing: 2px;
  }

  .logo-area {
    position: absolute;
    border-radius: 10px;
  }
  .logo-area-front {
    left: 110px;
    top: 140px;
    width: 180px;
    height: 260px;
    background: var(--navy);
  }
  .logo-area-back {
    left: 90px;
    top: 170px;
    width: 220px;
    height: 320px;
    background: linear-gradient(160deg, var(--navy-soft) 0%, var(--navy) 55%, var(--navy-deep) 100%);
  }

  .tab {
    position: absolute;
    left: 0;
    top: 452px;
    width: 26px;
    height: 46px;
    background: var(--navy);
    border-radius: 0 6px 6px 0;
  }

  .holder {
    position: absolute;
    left: 54px;
    top: 440px;
  }
  .holder-name {
    color: var(--navy);
    font-weight: 700;
    font-size: 27px;
    letter-spacing: .5px;
    line-height: 1.1;
  }
  .holder-role {
    color: var(--ink);
    font-weight: 400;
    font-size: 15px;
    letter-spacing: 1px;
    margin-top: 4px;
  }

  .address {
    position: absolute;
    left: 86px;
    top: 528px;
    color: var(--ink);
    font-size: 15px;
    line-height: 1.35;
    font-style: normal;
  }

  .contact-list {
    position: absolute;
    left: 86px;
    top: 592px;
    list-style: none;
    color: var(--ink);
    font-size: 15px;
  }
  .contact-list li {
    display: flex;
    align-items: center;
    gap: 10px;
    height: 26px;
  }
  .contact-list svg { width: 14px; height: 14px; fill: var(--navy); flex: none; }
</style>
</head>
<body>
  <section class="card card-front">
    <h1 class="firm-name">OAK PARTNERS</h1>

    <div class="logo-area logo-area-front" role="img" aria-label="Firm silhouette logo"></div>

    <span class="tab"></span>
    <div class="holder">
      <p class="holder-name">DORIAN PEMBERTON</p>
      <p class="holder-role">OWNER</p>
    </div>

    <address class="address">4120 Harbor Lane #310,<br>Fairview, CA 90000</address>

    <ul class="contact-list">
      <li>
        <svg viewBox="0 0 24 24" aria-hidden="true"><path d="M6.6 10.8a15.1 15.1 0 0 0 6.6 6.6l2.2-2.2a1 1 0 0 1 1-.25 11.4 11.4 0 0 0 3.6.57 1 1 0 0 1 1 1V20a1 1 0 0 1-1 1A17 17 0 0 1 3 4a1 1 0 0 1 1-1h3.5a1 1 0 0 1 1 1c0 1.25.2 2.45.57 3.570a1 1 0 0 1-.25 1z"/></svg>
        <span>800-555-0147</span>
      </li>
      <li>
        <svg viewBox="0 0 24 24" aria-hidden="true"><path d="M2 5h20v14H2zm2 2v.5l8 5 8-5V7zm0 2.9V17h16V9.9l-8 5z"/></svg>
        <span>dorian@oakpartners.example</span>
      </li>
      <li>
        <svg viewBox="0 0 24 24" aria-hidden="true"><path d="M12 2a10 10 0 1 0 0 20 10 10 0 0 0 0-20zm6.9 9h-3a15 15 0 0 0-1.3-5.6A8 8 0 0 1 18.9 11zM12 4c.9 1.2 1.8 3.6 1.9 7h-3.8C10.2 7.6 11.1 5.2 12 4zM9.4 5.4A15 15 0 0 0 8.1 11h-3a8 8 0 0 1 4.3-5.6zM5.1 13h3a15 15 0 0 0 1.3 5.6A8 8 0 0 1 5.1 13zm6.9 7c-.9-1.2-1.8-3.6-1.9-7h3.8c-.1 3.4-1 5.8-1.9 7zm2.6-1.4a15 15 0 0 0 1.3-5.6h3a8 8 0 0 1-4.3 5.6z"/></svg>
        <span>www.oakpartners.example</span>
      </li>
    </ul>
  </section>

  <section class="card card-back" aria-label="Card reverse">
    <div class="logo-area logo-area-back" role="img" aria-label="Embossed firm silhouette logo"></div>
  </section>
</body>
</html>
```